New Design for our Velostine Gran Reserva Brandy, it is the label design for the bottle label

We need a new bottle label for our Brandy Gran Reserva that we want to bring to the market.

Please have a look at all our current bottles and labels and the feel of our company under www.velostine-example.ch

The bottle that we will be using for the brand is a different one than the one that we already have, the design of the bottle is attached with a document.

I have also attached a briefing in regards to Brandy in general for your information.

### 1. What is Brandy?
Brandy is a distilled spirit made from fermented wine or other fruit wines. It is traditionally aged in oak barrels, which gives it its characteristic color and rich flavor. The aging process in oak is essential for developing the aromas and quality of the brandy.

### 2. What is Brandy Reserva?
A Brandy labeled as "Reserva" has undergone a longer aging process, typically at least 2 to 3 years, in oak barrels. This aging gives the brandy a deeper, more complex flavor profile and a darker color. "Reserva" is often an indication of higher quality.

### 3. Who enjoys drinking Brandy?
Brandy is typically favored by those who appreciate a deep, rich tasting experience. This often includes older consumers who value the time-aged complexity of the spirit. However, Brandy is also gaining popularity among younger people, especially through cocktails and modern serving styles.

### 4. Why is Brandy trending?
Brandy is experiencing a resurgence as consumers increasingly value quality and artisanal production methods. Its versatility in cocktails and association with traditional, luxurious experiences have also contributed to its renewed popularity.

### 5. What colors would be associated with Brandy?
The typical colors associated with Brandy are warm gold, amber, and deep golden-brown tones. These colors reflect the aging process in oak barrels and the richness of the flavors. Other associated colors might include dark brown and mahogany.

### 6. What is important to customers when buying Brandy?
Customers care about the origin of the Brandy, the aging time, the quality of the ingredients, the production method, and the brand. They also pay attention to the prestige of the product and the authenticity of the production.

### 7. What is not important to customers when buying Brandy?
For many customers, the price and packaging (unless it’s especially exclusive) may be less important than the quality and taste of the Brandy. The distillery name might be less significant if it isn’t tied to a particular reputation.

### 8. What do customers know about Swiss Brandy?
Swiss Brandy is still relatively unknown in many markets, but customers who are familiar with it appreciate the precision and quality of Swiss production. Swiss Brandy is assumed to be made with care and under strict quality standards.

### 9. What is Brandy Gran Reserva?
**Brandy Gran Reserva** is an even higher quality and longer-aged version of Brandy. Generally, a Gran Reserva is aged for at least 5 to 10 years or more in oak barrels. This extended aging process gives the Brandy an especially deep, complex flavor profile and often a darker, richer color. Gran Reserva is often regarded as the top-tier product within a Brandy range and appeals to discerning consumers who value quality, refinement, and a luxurious tasting experience.

The label “Gran Reserva” thus indicates the highest quality level for Brandies, similar to other spirits (like wine or whisky), where the aging time is a critical factor.

### 10. What emotions are associated with Brandy?
Brandy is often associated with luxury, relaxation, and comfort. It evokes feelings of tradition, elegance, and sophistication. Drinking Brandy is frequently seen as a moment of reflection and enjoyment.

### 11. How should Brandy be marketed?
Brandy should be marketed with a focus on its artisanal production, quality, and tradition. A narrative around the product, its aging, and origin can help create an emotional connection with the customer. The marketing should also emphasize the versatility of Brandy, whether consumed neat or in cocktails.

### 12. Sales test and label design for Velostine Brandy
For a sales test, I would suggest a tasting in an upscale setting, perhaps paired with a storytelling presentation highlighting the history of the 6-year aged Brandy and its aging in oak barrels.

**Label design**:
The label should reflect the exclusivity of the product, with an elegant, minimalist design. Colors like deep gold, mahogany, and a hint of deep blue could be used to emphasize the aging and quality of the Brandy. The label should include information about the aging time, the use of oak barrels, and a brief story about the Brandy’s production. A seal or embossing highlighting the craftsmanship would also be fitting.

Target Market(s)

Customers that like Brandy

Requirements
Must have
• the Alcohol % must be included on the label as well as our address.

```html
<!DOCTYPE html>
<html lang="en">
<head>
<meta charset="utf-8">
<title>Velostine Gran Reserva Brandy – Label Set</title>
<link href="https://fonts.googleapis.com/css2?family=Cinzel:wght@400;600;700&family=Cormorant+Garamond:ital,wght@0,500;1,400;1,500&family=Great+Vibes&display=swap" rel="stylesheet">
<style>
  :root{
    --page:#ffffff;
    --band-black:#141312;
    --band-black-soft:#1e1d1b;
    --mahogany:#4a1013;
    --gold:#b8913a;
    --gold-light:#d8b865;
    --gold-deep:#8c6a22;
    --cream:#efebe0;
    --ink:#5a5247;
    --ink-soft:#7d7466;
    --silver:#e8e8e8;
    --swiss-red:#e2231a;
    --white:#ffffff;
  }
  *{box-sizing:border-box;margin:0;padding:0}
  html,body{width:1200px;height:1200px;overflow:hidden;background:var(--page)}
  .canvas{position:relative;width:1200px;height:1200px}

  /* Neck label */
  .neck-label{
    position:absolute;left:110px;top:330px;width:124px;height:540px;
    background:var(--band-black);border-radius:8px;
    display:flex;align-items:center;justify-content:center;
  }
  .neck-label__text{
    writing-mode:vertical-rl;transform:rotate(180deg);
    display:flex;flex-direction:column;align-items:center;gap:4px;
  }
  .neck-label__title{font-family:"Cinzel",serif;font-weight:700;color:var(--gold);font-size:27px;letter-spacing:2px;white-space:nowrap}
  .neck-label__sub{font-family:"Cinzel",serif;color:var(--gold);font-size:11.5px;letter-spacing:1px;white-space:nowrap}
  .neck-label__script{font-family:"Great Vibes",cursive;color:var(--silver);font-size:38px;line-height:1;margin-top:14px}

  /* Front label */
  .front-label{
    position:absolute;left:290px;top:165px;width:800px;height:871px;
    background:var(--mahogany);border-radius:14px;overflow:hidden;
    text-align:center;
  }
  .front-label__band{
    position:absolute;left:0;top:0;width:100%;height:274px;
    background:linear-gradient(180deg,var(--band-black-soft),var(--band-black));
  }
  .front-label__rule{
    position:absolute;left:0;top:272px;width:100%;height:4px;
    background:linear-gradient(90deg,var(--gold-deep),var(--gold-light),var(--gold-deep));
  }
  .swiss-flag{position:absolute;left:387px;top:58px;width:26px;height:19px}
  .brand-name{
    position:absolute;left:0;right:0;top:96px;
    font-family:"Cinzel",serif;font-weight:700;font-size:46px;color:var(--gold);letter-spacing:1px;
  }
  .brand-tagline{
    position:absolute;left:0;right:0;top:164px;
    font-family:"Cinzel",serif;font-weight:600;font-size:11.5px;color:var(--white);letter-spacing:1.5px;
  }
  .seal{
    position:absolute;left:350px;top:224px;width:100px;height:100px;border-radius:50%;
    background:radial-gradient(circle at 40% 35%,var(--gold-light),var(--gold) 55%,var(--gold-deep));
    box-shadow:0 0 0 3px var(--mahogany),0 0 0 5px var(--gold-deep);
  }
  .product-title{
    position:absolute;left:0;right:0;top:340px;
    font-family:"Cinzel",serif;font-weight:700;font-size:50px;line-height:1;color:var(--gold);letter-spacing:3px;
  }
  .product-subtitle{
    position:absolute;left:0;right:0;top:397px;
    font-family:"Cinzel",serif;font-weight:600;font-size:19px;color:var(--gold);letter-spacing:2px;
  }
  .product-type{
    position:absolute;left:0;right:0;top:440px;
    font-family:"Great Vibes",cursive;font-size:98px;line-height:1;color:var(--silver);
  }

  /* Info panel with serrated edges */
  .info-panel{
    position:absolute;left:117px;top:598px;width:557px;height:192px;background:var(--cream);
    color:var(--ink);
  }
  .info-panel::before,.info-panel::after{
    content:"";position:absolute;left:0;width:100%;height:8px;
    background:
      linear-gradient(45deg,var(--cream) 50%,transparent 50%) 0 0/9px 8px repeat-x,
      linear-gradient(-45deg,var(--cream) 50%,transparent 50%) 0 0/9px 8px repeat-x;
  }
  .info-panel::before{top:-8px}
  .info-panel::after{bottom:-8px;transform:rotate(180deg)}
  .info-panel__story{
    position:absolute;left:30px;top:16px;width:200px;text-align:left;
    font-family:"Cormorant Garamond",serif;font-style:italic;font-size:11px;line-height:18px;color:var(--ink-soft);
  }
  .age-mark{position:absolute;left:240px;top:12px;width:72px;font-family:"Cinzel",serif;color:var(--ink)}
  .age-mark__label{display:block;font-size:15px;border-bottom:1px solid var(--ink-soft);border-top:1px solid var(--ink-soft);letter-spacing:1px}
  .age-mark__num{display:block;font-family:"Cormorant Garamond",serif;font-weight:500;font-size:62px;line-height:54px}
  .age-mark__unit{display:block;font-size:15px;border-top:1px solid var(--ink-soft);letter-spacing:1px}
  .tasting-notes{
    position:absolute;left:330px;top:16px;width:210px;text-align:left;list-style:none;
    font-family:"Cormorant Garamond",serif;font-style:italic;font-size:11px;line-height:19px;color:var(--ink-soft);
  }
  .tasting-notes li{border-bottom:1px solid #d8d2c4}
  .tasting-notes b{font-weight:500;color:var(--ink)}
  .cask-line{
    position:absolute;left:0;right:0;top:128px;display:flex;justify-content:center;align-items:center;gap:8px;
    font-family:"Cinzel",serif;font-size:15px;color:var(--ink-soft);letter-spacing:1px;
  }
  .cask-icon{width:36px;height:30px;border-radius:6px;background:linear-gradient(180deg,#b7b1a4,#8a8375)}
  .volume-line{
    position:absolute;left:0;right:0;top:166px;
    font-family:"Cinzel",serif;font-weight:600;font-size:12.5px;color:var(--gold-deep);letter-spacing:1px;
  }
  .producer-line{
    position:absolute;left:0;right:0;top:822px;
    font-family:"Cinzel",serif;font-weight:600;font-size:13px;color:var(--gold-deep);letter-spacing:1.5px;
  }
</style>
</head>
<body>
<main class="canvas">

  <section class="neck-label" aria-label="Neck label">
    <div class="neck-label__text">
      <span class="neck-label__title">Gran Reserva</span>
      <span class="neck-label__sub">Very Special Pot Still</span>
      <span class="neck-label__script">Brandy</span>
    </div>
  </section>

  <section class="front-label" aria-label="Front label">
    <div class="front-label__band" role="img" aria-label="Dark band with subtle black ornamental lattice pattern"></div>
    <div class="front-label__rule"></div>

    <svg class="swiss-flag" viewBox="0 0 26 19" aria-label="Swiss flag" role="img">
      <rect width="26" height="19" fill="var(--swiss-red)"/>
      <rect x="11.5" y="4.5" width="3" height="10" fill="var(--white)"/>
      <rect x="8" y="8" width="10" height="3" fill="var(--white)"/>
    </svg>

    <div class="brand-name">Velostine</div>
    <div class="brand-tagline">SWISS DISTILLERY</div>

    <div class="seal" role="img" aria-label="Gold seal emblem"></div>

    <h1 class="product-title">Gran Reserva</h1>
    <p class="product-subtitle">Very Special Pot Still</p>
    <p class="product-type">Brandy</p>

    <div class="info-panel">
      <p class="info-panel__story">This brandy is crafted from carefully selected grapes, distilled in Copper Pot Stills, and aged for at least 6 years in French Oak Barrels. The long aging process allows the Brandy to develop complex flavors and a smooth, rich character.</p>
      <div class="age-mark">
        <span class="age-mark__label">Aged</span>
        <span class="age-mark__num">6</span>
        <span class="age-mark__unit">Years</span>
      </div>
      <ul class="tasting-notes">
        <li><b>Colour:</b> rich golden colour</li>
        <li><b>Aroma:</b> ripe apple with hints of vanilla</li>
        <li><b>Taste:</b> spicy with fruity palate</li>
        <li><b>Finish:</b> well balanced with a fruity aftertaste</li>
      </ul>
      <div class="cask-line">
        <span>Aged in French</span>
        <span class="cask-icon" role="img" aria-label="Oak barrels illustration"></span>
        <span>Oak Barrels</span>
      </div>
      <div class="volume-line">45% Alc. Vol. &nbsp;|&nbsp; 750 ml</div>
    </div>

    <p class="producer-line">Produced by Velostine Swiss Distillery, Switzerland</p>
  </section>

</main>
</body>
</html>
```